Business Card For Halvenmoor Financial Consulting

Hi, I would like a business card designed. Bold, modern.
Please use the same design as the logo. I have also attached the website design to see the overall theme.
Wordmark Font
Color: Hex: #01AEF7

```html
<!DOCTYPE html>
<html lang="en">
<head>
<meta charset="utf-8">
<title>Halvenmoor Financial Consulting – Business Card</title>
<link rel="stylesheet" href="https://fonts.googleapis.com/css2?family=Montserrat:wght@600&family=Open+Sans:wght@400;600&display=swap">
<style>
  :root {
    --canvas-bg: #d9d4ce;
    --card-bg: #eeeae5;
    --navy: #0b3a4f;
    --band-top: #175a74;
    --band-bottom: #0a3347;
    --name-teal: #3c94ae;
    --soft-text: #d8cfc4;
  }
  * { margin: 0; padding: 0; box-sizing: border-box; }
  html, body { width: 1200px; height: 1047px; overflow: hidden; }
  body { background: var(--canvas-bg); position: relative; font-family: "Open Sans", sans-serif; }
  .card {
    position: absolute; left: 100px; top: 251px; width: 1000px; height: 545px;
    border-radius: 26px; overflow: hidden; background: var(--card-bg);
    box-shadow: 0 14px 40px rgba(0,0,0,0.18);
  }
  .card__band { position: absolute; inset: 0; width: 1000px; height: 545px; }
  .brand {
    position: absolute; right: 40px; top: 48px; text-align: right;
    font-family: "Open Sans", sans-serif; font-weight: 600; color: var(--navy);
    font-size: 31px; line-height: 1.2; letter-spacing: 1px; text-transform: uppercase;
  }
  .person { position: absolute; left: 45px; top: 262px; }
  .person__name { font-weight: 600; font-size: 36px; color: var(--name-teal); letter-spacing: 0.5px; }
  .person__title { font-size: 25px; color: var(--soft-text); margin-top: 2px; }
  .contact { position: absolute; left: 45px; top: 394px; list-style: none; }
  .contact__item { display: flex; align-items: center; gap: 10px; font-size: 26px; color: var(--soft-text); height: 37px; }
  .contact__icon { width: 20px; height: 20px; fill: var(--name-teal); }
  .address { position: absolute; right: 40px; top: 433px; text-align: right; font-size: 26px; line-height: 37px; color: var(--soft-text); }
</style>
</head>
<body>
  <div class="card">
    <svg class="card__band" viewBox="0 0 1000 545" aria-hidden="true">
      <defs>
        <linearGradient id="bandShade" x1="0" y1="0" x2="1" y2="1">
          <stop offset="0" stop-color="var(--band-top)"/>
          <stop offset="1" stop-color="var(--band-bottom)"/>
        </linearGradient>
      </defs>
      <path d="M0,205 C300,150 600,250 1000,290 L1000,545 L0,545 Z" fill="url(#bandShade)"/>
    </svg>

    <div class="brand">Halvenmoor<br>Financial Consulting</div>

    <div class="person">
      <div class="person__name">MARCUS ELLERY</div>
      <div class="person__title">Managing Director</div>
    </div>

    <ul class="contact">
      <li class="contact__item">
        <svg class="contact__icon" viewBox="0 0 24 24"><path d="M6.6 10.8a15.1 15.1 0 0 0 6.6 6.6l2.2-2.2a1 1 0 0 1 1-.25 11.4 11.4 0 0 0 3.6.57 1 1 0 0 1 1 1V20a1 1 0 0 1-1 1A17 17 0 0 1 3 4a1 1 0 0 1 1-1h3.5a1 1 0 0 1 1 1c0 1.25.2 2.45.57 3.57a1 1 0 0 1-.25 1z"/></svg>
        123 456 789
      </li>
      <li class="contact__item">
        <svg class="contact__icon" viewBox="0 0 24 24"><path d="M3 5h18v14H3z M3 6l9 7 9-7" fill="var(--name-teal)" stroke="var(--band-bottom)" stroke-width="1.5"/></svg>
        info@youremail.com
      </li>
      <li class="contact__item">
        <svg class="contact__icon" viewBox="0 0 24 24"><circle cx="12" cy="12" r="9"/><path d="M3 12h18M12 3c3 3 3 15 0 18M12 3c-3 3-3 15 0 18" fill="none" stroke="var(--band-bottom)" stroke-width="1.4"/></svg>
        www.yourwebsite.com
      </li>
    </ul>

    <div class="address">Your address, City<br>State, Zip 1234</div>
  </div>
</body>
</html>
```